Letterhead for a German Distribution/Manufacturing Company

We need a professional Letterhead in a unique Design.
not to playful.
The Letterhead has to show show that we are a international company with headquater in Germany.
all details like adress, Vat Tax Number, Bank Accout, Eori, email, Company number has to be on the Letterhead.
for example use: VAT TAX DE5470318 Bank Account: Kestrel Bank IBAN DE412058731ß204683 Swift: MORV0417352 EORI 3150428697 Company Number: HRB 51806 Adress: VOLMINTA UG Ahornweg 7 Postal Code 06384 City Lindenhain Country: Germany Email: info@volminta-example.com
the design can be colored but doesnt have to be
Industry/Entity Type
Manufacturing and international distribution
Requirements
Must have
- show that we are a international company with headquater in Germany. our company infos and logo

```html
<!DOCTYPE html>
<html lang="en">
<head>
<meta charset="utf-8">
<title>VOLMINTA Letterhead</title>
<link href="https://fonts.googleapis.com/css2?family=Open+Sans:wght@400;600&display=swap" rel="stylesheet">
<style>
  :root {
    --backdrop: #ececec;
    --paper: #f6f6f7;
    --band: #4a4a4a;
    --rule: #9a9a9a;
    --ink: #3e3e3e;
    --brand-ink: #ffffff;
  }
  * { margin: 0; padding: 0; box-sizing: border-box; }
  html, body {
    width: 1200px;
    height: 900px;
    overflow: hidden;
    background: var(--backdrop);
    font-family: "Open Sans", sans-serif;
  }
  .canvas {
    width: 1200px;
    height: 900px;
    display: flex;
    align-items: center;
    justify-content: center;
  }
  .letterhead {
    position: relative;
    width: 594px;
    height: 840px;
    background: var(--paper);
    box-shadow: 0 2px 10px rgba(0,0,0,0.12);
  }
  .letterhead__header {
    position: absolute;
    top: 0; left: 0; right: 0;
    height: 104px;
    background: var(--band);
    display: flex;
    align-items: center;
    justify-content: center;
  }
  .letterhead__header-rule {
    position: absolute;
    top: 110px; left: 0; right: 0;
    height: 1px;
    background: var(--rule);
  }
  .brand {
    display: flex;
    align-items: center;
    gap: 10px;
    color: var(--brand-ink);
  }
  .brand__mark {
    width: 18px;
    height: 18px;
    border-radius: 50%;
    background: var(--brand-ink);
  }
  .brand__name {
    font-size: 26px;
    font-weight: 400;
    letter-spacing: 1.5px;
  }
  .letterhead__footer-info {
    position: absolute;
    left: 40px; right: 40px;
    bottom: 62px;
    text-align: center;
    color: var(--ink);
    font-size: 10.5px;
    line-height: 1.55;
    font-style: normal;
  }
  .letterhead__footer-info .label { font-weight: 600; }
  .letterhead__footer-rule {
    position: absolute;
    bottom: 42px; left: 0; right: 0;
    height: 1px;
    background: var(--rule);
  }
  .letterhead__footer {
    position: absolute;
    bottom: 0; left: 0; right: 0;
    height: 36px;
    background: var(--band);
  }
</style>
</head>
<body>
<main class="canvas">
  <article class="letterhead">
    <header class="letterhead__header">
      <div class="brand">
        <span class="brand__mark"></span>
        <span class="brand__name">VOLMINTA</span>
      </div>
    </header>
    <div class="letterhead__header-rule"></div>

    <address class="letterhead__footer-info">
      <p><span class="label">VAT No.</span> TAX DE5470318 | <span class="label">Company No.</span> HRB 51806</p>
      <p>Bank A/c. Kestrel Bank IBAN DE412058731ß204683 | <span class="label">Swift A/c.</span> MORV0417352 EORI 3150428697</p>
      <p>E. info@volminta-example.com</p>
      <p>VOLMINTA UG Ahornweg 7 Postal Code 06384 City Lindenhain, Germany</p>
    </address>
    <div class="letterhead__footer-rule"></div>
    <footer class="letterhead__footer"></footer>
  </article>
</main>
</body>
</html>
```